Corvane Paintless Dent Removal

Our company works on vehicles removing dents using a highly skilled trade which the metal is massaged out with special tools without disturbing the original paint, hence paintless dent removal. Besides keeping the paint and metal original its also very environmentally friendly since no paint or toxic fillers are used. Also we we are one of the most experienced companies in the business with 25 years

Target Market(s)

Retail Automobile consumers, Auto Dealerships and Auto Body Shops

Industry/Entity Type

Auto Repair

Contact Information for Business Card

Dale Hollister
PO Box 518 Brookmere, NY 11962
631-555-0148
corvanepdr@mailbox-example.com
website corvanepdr.example
youtube corvane paintless dent removal
25 years of experience removing Dents, Dings and Hail Damage

Font styles to use
Serif
Sans Serif

Colors

Designer to choose colors to be used in the design.

Requirements
Must have
• I do like things that are simple but classy and somewhat bold, also I like my logo so that should be somewhat important

```html
<!DOCTYPE html>
<html lang="en">
<head>
<meta charset="utf-8">
<title>Corvane Paintless Dent Removal – Business Card</title>
<link rel="stylesheet" href="https://fonts.googleapis.com/css2?family=Roboto:wght@400;700&display=swap">
<style>
  :root {
    --backdrop: #b9b9b9;
    --navy: #13254a;
    --green: #78bc2a;
    --card-light: #f4f4f4;
    --text-dark: #1c2a4d;
    --text-body: #2f3645;
    --text-on-navy: #e6e9ef;
    --video-red: #d9262a;
  }
  * { box-sizing: border-box; margin: 0; padding: 0; }
  html, body { width: 1200px; height: 576px; overflow: hidden; }
  body {
    background: var(--backdrop);
    font-family: "Roboto", Arial, sans-serif;
    position: relative;
  }
  .card {
    position: absolute;
    top: 138px;
    width: 484px;
    height: 294px;
    border-radius: 14px;
    overflow: hidden;
  }
  .card-front { left: 82px; background: var(--navy); }
  .card-back { left: 602px; background: var(--card-light); color: var(--text-body); }

  .brand-name {
    position: absolute;
    font-weight: 700;
    text-align: center;
    line-height: 1.1;
  }
  .card-front .brand-name {
    left: 0; right: 0; top: 108px;
    font-size: 30px;
    color: #ffffff;
  }
  .card-back .brand-name {
    left: 190px; right: 10px; top: 48px;
    font-size: 19px;
    color: var(--navy);
  }

  .front-web {
    position: absolute;
    left: 0; right: 0; top: 262px;
    display: flex; align-items: center; justify-content: center; gap: 16px;
    font-size: 12px; letter-spacing: 0.5px; color: var(--text-on-navy);
  }
  .front-web .rule { width: 92px; height: 1px; background: var(--green); }
  .front-web .accent { color: var(--green); }

  .holder-name {
    position: absolute; left: 19px; top: 148px;
    font-size: 21px; font-weight: 700; color: var(--text-dark);
  }
  .holder-rule {
    position: absolute; left: 163px; right: 22px; top: 177px;
    height: 1.5px; background: var(--green);
  }
  .holder-title {
    position: absolute; left: 19px; top: 178px;
    font-size: 11.5px; color: var(--text-body);
  }
  .contact-list {
    position: absolute; left: 19px; top: 218px;
    list-style: none; font-size: 12px; line-height: 16.5px;
  }
  .contact-list li { display: flex; align-items: center; gap: 12px; }
  .contact-list svg { width: 10px; height: 10px; flex: none; }
  .postal {
    position: absolute; right: 22px; top: 218px;
    text-align: right; font-size: 12px; line-height: 16.5px;
  }
  .video-link { display: flex; align-items: center; justify-content: flex-end; gap: 9px; }
  .video-mark { width: 15px; height: 11px; border-radius: 3px; background: var(--video-red); }
</style>
</head>
<body>

<section class="card card-front" aria-label="Card front">
  <div class="brand-name">Corvane Paintless<br>Dent Removal</div>
  <div class="front-web">
    <span class="rule"></span>
    <span>www.<span class="accent">corvanepdr</span>.example</span>
    <span class="rule"></span>
  </div>
</section>

<section class="card card-back" aria-label="Card back">
  <div class="brand-name">Corvane Paintless<br>Dent Removal</div>

  <div class="holder-name">Dale Hollister</div>
  <div class="holder-rule"></div>
  <div class="holder-title">Managing Director</div>

  <ul class="contact-list">
    <li>
      <svg viewBox="0 0 10 10" aria-hidden="true"><path fill="#78bc2a" d="M1 3.5C1 2 2 1.5 5 1.5S9 2 9 3.5L7.5 4 7 3H3L2.5 4zM2.5 5h5l1 3.5h-7z"/></svg>
      631-555-0148
    </li>
    <li>
      <svg viewBox="0 0 10 10" aria-hidden="true"><rect x="0.5" y="2" width="9" height="6.5" fill="#78bc2a"/><path d="M0.5 2.3L5 5.8 9.5 2.3" stroke="#f4f4f4" stroke-width="1" fill="none"/></svg>
      corvanepdr@mailbox-example.com
    </li>
    <li>
      <svg viewBox="0 0 10 10" aria-hidden="true"><circle cx="5" cy="5" r="4.2" fill="none" stroke="#78bc2a" stroke-width="1.2"/><path d="M0.8 5h8.4M5 0.8c-2.2 2.4-2.2 6 0 8.4M5 0.8c2.2 2.4 2.2 6 0 8.4" stroke="#78bc2a" stroke-width="0.9" fill="none"/></svg>
      www.corvanepdr.example
    </li>
  </ul>

  <div class="postal">
    <div>PO Box 518 Brookmere,</div>
    <div>NY 11962</div>
    <div class="video-link"><span class="video-mark" aria-hidden="true"></span>videos.example/Dale Hollister</div>
  </div>
</section>

</body>
</html>
```